UX Design for Analytics Web Application

http://velqoranthe.com/
We are tech & consulting company with analytics products (web applications), located at Rio de Janeiro, Brazil.

We are searching a partner do develop UX for our products, i.e, aesthetics, usability, HTML/CSS.

Currently we have a product suite and the goal is to make a pilot re-design project with one of our products.

The product of interest is interactive webapp that aims at data analysis, significantly different from blogs, e-commerce or landing pages.

We do have a software development team but we lack an UX & HTML expert. Currently we use Bootstrap templates but the results are insatisfatory.

So, the project scope is, to develop the arts (UX, aesthetics, etc) along with the code/mockup (HTML/CSS) for one of our product (3 pages).

This is a pilot project and there's potential to rehire for our other products. Code quality is of importance.

More details and specification can be found in attached files.

Target Market(s)

Executives, managers & consultants

Industry/Entity Type

It Company

Coding

Coded - Design and coding required

Number of Pages Required

3 page

Font styles to use
Sans Serif

Requirements
Must have
• (see attached files, prefer the pptx version))
• -Responsive
Nice to have
• (see attached files, prefer the pptx version)
Should not have
• -Avoid Green, Red and Yellow colors. They have a meaning of good, bad and average in our products.

```html
<!DOCTYPE html>
<html lang="en">
<head>
<meta charset="utf-8">
<title>Analytics Dashboard</title>
<link rel="stylesheet" href="https://fonts.googleapis.com/css2?family=Roboto:wght@300;400;500;700&display=swap">
<style>
:root{
  --topbar:#222d38;
  --page:#f0f0f0;
  --card:#ffffff;
  --ink:#2b2f33;
  --muted:#5f6770;
  --line:#e6e8ea;
  --blue:#39a9dc;
  --indigo:#5c6bc0;
  --violet:#8e44ad;
  --slate:#2f7896;
  --direct:#5c6bc0;
  --email:#90caf9;
  --advert:#9575cd;
  --video:#d6cbee;
  --search:#39a9dc;
  --yearly:#3f4f9e;
  --year-top:#8fdcfa;
  --year-bottom:#3a9be0;
  --browser:#6a3fa0;
  --phones:#2c5f8a;
  --badge-alert:#7e57c2;
  --badge-blue:#2f9fd8;
  --status:#4fc3f7;
}
*{box-sizing:border-box;margin:0;padding:0}
html,body{width:1200px;height:689px;overflow:hidden}
body{font-family:"Roboto",Arial,sans-serif;background:var(--page);color:var(--ink);position:relative}

.topbar{position:absolute;left:0;top:0;width:1200px;height:53px;background:var(--topbar);color:#fff;font-size:14px}
.topbar svg{position:absolute;top:17px}
.topbar .label{position:absolute;top:18px}
.badge{position:absolute;top:7px;min-width:19px;height:19px;border-radius:10px;font-size:11px;line-height:19px;text-align:center;color:#fff}
.badge.alerts{left:978px;background:var(--badge-alert)}
.badge.messages{left:1031px;background:var(--badge-blue)}
.avatar{position:absolute;left:1073px;top:13px;width:27px;height:27px;border-radius:50%;background:linear-gradient(#c8b8a6,#7d6a5a)}
.avatar-status{position:absolute;left:1091px;top:31px;width:9px;height:9px;border-radius:50%;background:var(--status);border:2px solid var(--topbar)}
.flag{position:absolute;left:869px;top:20px;width:18px;height:12px;background:linear-gradient(#b73a46 0 50%,#fff 50% 60%,#b73a46 60%)}
.flag::before{content:"";position:absolute;left:0;top:0;width:8px;height:7px;background:#33467a}

.sidebar{position:absolute;left:0;top:53px;width:140px;height:636px;background:var(--card);box-shadow:1px 0 3px rgba(0,0,0,.08)}
.nav-item{position:absolute;left:0;width:140px;text-align:center;font-size:13px;color:#333}
.nav-item svg{display:block;margin:0 auto 7px}

.card{position:absolute;background:var(--card);box-shadow:0 1px 2px rgba(0,0,0,.05);overflow:hidden}
.card-title{position:absolute;left:20px;top:13px;font-size:17px;font-weight:500}
.refresh{position:absolute;top:15px}

.stats{left:164px;top:76px;width:1012px;height:148px;display:grid;grid-template-columns:repeat(4,1fr)}
.stat{position:relative;border-right:1px solid var(--line);margin:20px 0}
.stat:last-child{border-right:none}
.stat-icon{position:absolute;left:33px;top:16px}
.stat-value{position:absolute;right:26px;top:4px;font-size:40px;font-weight:300;letter-spacing:-.5px}
.stat-label{position:absolute;left:33px;top:58px;font-size:13px;color:var(--muted)}
.stat-delta{position:absolute;right:26px;top:58px;font-size:13px}
.stat-track{position:absolute;left:33px;right:26px;top:83px;height:6px;background:#e9ebed}
.stat-fill{height:6px}

.campaigns{left:164px;top:250px;width:665px;height:380px}
.yearly{left:858px;top:250px;width:318px;height:380px;background:var(--yearly);color:#fff}
.browser{left:164px;top:657px;width:491px;height:120px;background:var(--browser);color:#fff}
.phones{left:683px;top:657px;width:493px;height:120px;background:var(--phones);color:#fff}
.chart{position:absolute;left:0;top:0}
.chart text{font-family:"Roboto",Arial,sans-serif}
</style>
</head>
<body>

<header class="topbar">
  <svg style="left:27px" width="18" height="16" viewBox="0 0 18 16"><path d="M1 3h16M1 8h16M1 13h16" stroke="#fff" stroke-width="2"/></svg>
  <svg style="left:79px" width="16" height="16" viewBox="0 0 16 16"><circle cx="6.5" cy="6.5" r="5" fill="none" stroke="#fff" stroke-width="2"/><path d="M10 10l5 5" stroke="#fff" stroke-width="2"/></svg>
  <svg style="left:127px" width="15" height="15" viewBox="0 0 15 15" fill="none" stroke="#fff" stroke-width="1.8"><path d="M1 5V1h4M10 1h4v4M14 10v4h-4M5 14H1v-4"/></svg>
  <span class="label" style="left:171px">Mega</span>
  <svg style="left:207px;top:21px" width="9" height="6" viewBox="0 0 9 6"><path d="M1 1l3.5 3.5L8 1" fill="none" stroke="#fff" stroke-width="1.3"/></svg>

  <span class="flag"></span>
  <span class="label" style="left:894px">English</span>
  <svg style="left:942px;top:21px" width="9" height="6" viewBox="0 0 9 6"><path d="M1 1l3.5 3.5L8 1" fill="none" stroke="#fff" stroke-width="1.3"/></svg>
  <svg style="left:966px;top:18px" width="18" height="18" viewBox="0 0 18 18" fill="none" stroke="#fff" stroke-width="1.7"><path d="M4 13V8a5 5 0 0 1 10 0v5l1.5 1.5h-13z"/><path d="M7.5 16.5h3"/></svg>
  <span class="badge alerts">5</span>
  <svg style="left:1020px;top:20px" width="17" height="13" viewBox="0 0 17 13" fill="none" stroke="#fff" stroke-width="1.7"><rect x="1" y="1" width="15" height="11" rx="1"/><path d="M1 2l7.5 5.5L16 2"/></svg>
  <span class="badge messages">8</span>
  <span class="avatar" role="img" aria-label="User profile photo"></span>
  <span class="avatar-status"></span>
  <span class="label" style="left:1111px">John Doe</span>
  <svg style="left:1171px;top:21px" width="9" height="6" viewBox="0 0 9 6"><path d="M1 1l3.5 3.5L8 1" fill="none" stroke="#fff" stroke-width="1.3"/></svg>
</header>

<nav class="sidebar">
  <div class="nav-item" style="top:12px">
    <svg width="22" height="20" viewBox="0 0 22 20"><path d="M11 1L1 10h3v9h5v-6h4v6h5v-9h3z" fill="#333"/></svg>Dashboard</div>
  <div class="nav-item" style="top:85px">
    <svg width="20" height="20" viewBox="0 0 20 20" fill="none" stroke="#333" stroke-width="1.8"><rect x="6" y="1" width="12" height="14" rx="1"/><path d="M3 5v13h11"/></svg>Templates</div>
  <div class="nav-item" style="top:158px">
    <svg width="20" height="20" viewBox="0 0 20 20" fill="none" stroke="#333" stroke-width="1.8"><rect x="2" y="2" width="16" height="16" rx="1"/><path d="M2 7h16M8 7v11"/></svg>Layouts</div>
  <div class="nav-item" style="top:231px">
    <svg width="22" height="20" viewBox="0 0 22 20" fill="none" stroke="#333" stroke-width="1.8"><path d="M2 3h6l2 2h10v12H2z"/></svg>General</div>
  <div class="nav-item" style="top:304px">
    <svg width="18" height="20" viewBox="0 0 18 20" fill="none" stroke="#333" stroke-width="1.8"><rect x="2" y="1" width="14" height="18" rx="1"/><path d="M5 6h8M5 10h8M5 14h6"/></svg>Pages</div>
  <div class="nav-item" style="top:377px">
    <svg width="20" height="20" viewBox="0 0 20 20" fill="none" stroke="#333" stroke-width="1.8"><path d="M3 17L17 3c1 3-1 8-5 11-3 2-6 2-9 3zM3 17l6-6"/></svg>UI</div>
  <div class="nav-item" style="top:450px">
    <svg width="18" height="20" viewBox="0 0 18 20" fill="none" stroke="#333" stroke-width="1.8"><rect x="2" y="2" width="14" height="16" rx="1"/><path d="M5 7h8M5 11h8M5 15h5"/></svg>Forms</div>
  <div class="nav-item" style="top:523px">
    <svg width="20" height="18" viewBox="0 0 20 18" fill="none" stroke="#333" stroke-width="1.8"><rect x="1" y="1" width="18" height="16"/><path d="M1 6h18M1 11.5h18M7 1v16M13 1v16"/></svg>Tables</div>
  <div class="nav-item" style="top:596px">
    <svg width="20" height="20" viewBox="0 0 20 20" fill="none" stroke="#333" stroke-width="1.8"><rect x="2" y="2" width="16" height="16" rx="1"/><path d="M10 6v8M6 10h8"/></svg>Widgets</div>
</nav>

<section class="card stats">
  <div class="stat">
    <svg class="stat-icon" width="24" height="24" viewBox="0 0 24 24" fill="none" stroke="#4a5560" stroke-width="1.7"><path d="M12 2l9 5v10l-9 5-9-5V7z"/><path d="M3 7l9 5 9-5M12 12v10"/></svg>
    <span class="stat-value" style="color:var(--blue)">5,879</span>
    <span class="stat-label">Total Products</span>
    <span class="stat-delta" style="color:var(--blue)">↑ 16.89%</span>
    <div class="stat-track"><div class="stat-fill" style="width:80%;background:var(--blue)"></div></div>
  </div>
  <div class="stat">
    <svg class="stat-icon" width="24" height="24" viewBox="0 0 24 24" fill="none" stroke="#4a5560" stroke-width="1.7"><path d="M3 3h8l10 10-8 8L3 11z"/><circle cx="7.5" cy="7.5" r="1.5"/></svg>
    <span class="stat-value" style="color:var(--indigo)">423</span>
    <span class="stat-label">New Orders</span>
    <span class="stat-delta" style="color:var(--indigo)">↑ 5.14%</span>
    <div class="stat-track"><div class="stat-fill" style="width:45%;background:var(--indigo)"></div></div>
  </div>
  <div class="stat">
    <svg class="stat-icon" width="26" height="24" viewBox="0 0 26 24" fill="none" stroke="#4a5560" stroke-width="1.7"><path d="M2 6h5c5 0 7 12 12 12h4M2 18h5c2 0 3-2 4-4M15 8c1-1 2-2 4-2h4M20 3l3 3-3 3M20 15l3 3-3 3"/></svg>
    <span class="stat-value" style="color:var(--violet)">61%</span>
    <span class="stat-label">Conversion Rate</span>
    <span class="stat-delta" style="color:var(--violet)">↓ 2.24%</span>
    <div class="stat-track"><div class="stat-fill" style="width:75%;background:var(--violet)"></div></div>
  </div>
  <div class="stat">
    <svg class="stat-icon" width="16" height="26" viewBox="0 0 16 26" fill="none" stroke="#4a5560" stroke-width="2.2"><path d="M13 7c-1-2-3-3-5-3-3 0-5 1.5-5 4 0 5 10 3 10 9 0 2.5-2 4-5 4-2.5 0-4.5-1-5.5-3M8 1v24"/></svg>
    <span class="stat-value" style="color:var(--slate)">$6,87M</span>
    <span class="stat-label">Total Profit</span>
    <span class="stat-delta" style="color:var(--slate)">↑ 43.84%</span>
    <div class="stat-track"><div class="stat-fill" style="width:60%;background:var(--slate)"></div></div>
  </div>
</section>

<section class="card campaigns">
  <h2 class="card-title">Sales by Campaigns</h2>
  <svg class="refresh" style="left:624px" width="14" height="14" viewBox="0 0 14 14" fill="none" stroke="#8a9096" stroke-width="1.5"><path d="M12 7a5 5 0 1 1-1.5-3.6M11 1v3H8"/></svg>
  <svg class="chart" width="665" height="380" viewBox="0 0 665 380">
    <g font-size="12" fill="#333">
      <rect x="40" y="83" width="19" height="11" rx="2" fill="var(--direct)"/><text x="64" y="93">Direct access</text>
      <rect x="154" y="83" width="19" height="11" rx="2" fill="var(--email)"/><text x="178" y="93">Email marketing</text>
      <rect x="284" y="83" width="19" height="11" rx="2" fill="var(--advert)"/><text x="308" y="93">Advertising alliance</text>
      <rect x="435" y="83" width="19" height="11" rx="2" fill="var(--video)"/><text x="459" y="93">Video ads</text>
      <rect x="529" y="83" width="19" height="11" rx="2" fill="var(--search)"/><text x="553" y="93">Search engine</text>
    </g>
    <g stroke="#e0e2e4" stroke-width="1">
      <path d="M58 121H608M58 175H608M58 229H608M58 283H608"/>
      <path d="M136.6 121V337M215.1 121V337M293.7 121V337M372.3 121V337M450.9 121V337M529.4 121V337M608 121V337"/>
    </g>
    <path d="M58 121V337H608" fill="none" stroke="#555" stroke-width="1"/>
    <g font-size="12" fill="#333" text-anchor="end">
      <text x="52" y="125">2,000</text><text x="52" y="179">1,500</text><text x="52" y="233">1,000</text><text x="52" y="287">500</text><text x="52" y="341">0</text>
    </g>
    <g font-size="12" fill="#333" text-anchor="middle">
      <text x="97" y="356">Mon</text><text x="176" y="356">Tue</text><text x="254" y="356">Wed</text><text x="333" y="356">Thu</text><text x="411" y="356">Fri</text><text x="490" y="356">Sat</text><text x="569" y="356">Sun</text>
    </g>
    <g transform="translate(58 337) scale(1 -0.108)">
      <g>
        <rect x="8" y="0" width="18" height="330" fill="var(--direct)"/>
        <rect x="32" y="0" width="18" height="100" fill="var(--email)"/><rect x="32" y="100" width="18" height="200" fill="var(--advert)"/><rect x="32" y="300" width="18" height="200" fill="var(--video)"/>
        <rect x="55" y="0" width="17" height="870" fill="var(--search)"/>
      </g>
      <g transform="translate(78.6 0)">
        <rect x="8" y="0" width="18" height="330" fill="var(--direct)"/>
        <rect x="32" y="0" width="18" height="130" fill="var(--email)"/><rect x="32" y="130" width="18" height="190" fill="var(--advert)"/><rect x="32" y="320" width="18" height="230" fill="var(--video)"/>
        <rect x="55" y="0" width="17" height="1020" fill="var(--search)"/>
      </g>
      <g transform="translate(157.1 0)">
        <rect x="8" y="0" width="18" height="310" fill="var(--direct)"/>
        <rect x="32" y="0" width="18" height="110" fill="var(--email)"/><rect x="32" y="110" width="18" height="180" fill="var(--advert)"/><rect x="32" y="290" width="18" height="210" fill="var(--video)"/>
        <rect x="55" y="0" width="17" height="970" fill="var(--search)"/>
      </g>
      <g transform="translate(235.7 0)">
        <rect x="8" y="0" width="18" height="330" fill="var(--direct)"/>
        <rect x="32" y="0" width="18" height="130" fill="var(--email)"/><rect x="32" y="130" width="18" height="240" fill="var(--advert)"/><rect x="32" y="370" width="18" height="160" fill="var(--video)"/>
        <rect x="55" y="0" width="17" height="1030" fill="var(--search)"/>
      </g>
      <g transform="translate(314.3 0)">
        <rect x="8" y="0" width="18" height="400" fill="var(--direct)"/>
        <rect x="32" y="0" width="18" height="80" fill="var(--email)"/><rect x="32" y="80" width="18" height="300" fill="var(--advert)"/><rect x="32" y="380" width="18" height="200" fill="var(--video)"/>
        <rect x="55" y="0" width="17" height="1700" fill="var(--search)"/>
      </g>
      <g transform="translate(392.9 0)">
        <rect x="8" y="0" width="18" height="330" fill="var(--direct)"/>
        <rect x="32" y="0" width="18" height="230" fill="var(--email)"/><rect x="32" y="230" width="18" height="330" fill="var(--advert)"/><rect x="32" y="560" width="18" height="340" fill="var(--video)"/>
        <rect x="55" y="0" width="17" height="1610" fill="var(--search)"/>
      </g>
      <g transform="translate(471.4 0)">
        <rect x="8" y="0" width="18" height="330" fill="var(--direct)"/>
        <rect x="32" y="0" width="18" height="210" fill="var(--email)"/><rect x="32" y="210" width="18" height="120" fill="var(--advert)"/><rect x="32" y="330" width="18" height="610" fill="var(--video)"/>
        <rect x="55" y="0" width="17" height="1580" fill="var(--search)"/>
      </g>
    </g>
    <path d="M122 243L430 155" stroke="var(--search)" stroke-width="1.3" stroke-dasharray="5 4" fill="none"/>
    <path d="M437 153l-9 -1 3 7z" fill="var(--search)"/>
  </svg>
</section>

<section class="card yearly">
  <h2 class="card-title">Yearly Sales</h2>
  <svg class="refresh" style="left:286px" width="14" height="14" viewBox="0 0 14 14" fill="none" stroke="#fff" stroke-width="1.5"><path d="M12 7a5 5 0 1 1-1.5-3.6M11 1v3H8"/></svg>
  <svg class="chart" width="318" height="380" viewBox="0 0 318 380">
    <defs>
      <linearGradient id="yearBar" x1="0" y1="0" x2="0" y2="1">
        <stop offset="0" stop-color="var(--year-top)"/><stop offset="1" stop-color="var(--year-bottom)"/>
      </linearGradient>
    </defs>
    <g stroke="rgba(255,255,255,.18)" stroke-width="1">
      <path d="M52 70H305M52 113H305M52 156H305M52 199H305M52 242H305M52 285H305M52 328H305"/>
    </g>
    <g font-size="11" fill="#fff" fill-opacity=".85" text-anchor="end">
      <text x="43" y="74">3000</text><text x="43" y="117">2500</text><text x="43" y="160">2000</text><text x="43" y="203">1500</text><text x="43" y="246">1000</text><text x="43" y="289">500</text><text x="43" y="332">0</text>
    </g>
    <g fill="#000" fill-opacity=".14">
      <rect x="58" y="70" width="23" height="258"/><rect x="96.7" y="70" width="23" height="258"/><rect x="135.4" y="70" width="23" height="258"/><rect x="174.1" y="70" width="23" height="258"/><rect x="212.8" y="70" width="23" height="258"/><rect x="251.5" y="70" width="23" height="258"/>
    </g>
    <g fill="url(#yearBar)">
      <rect x="58" y="166.3" width="23" height="161.7"/>
      <rect x="96.7" y="130.2" width="23" height="197.8"/>
      <rect x="135.4" y="131.1" width="23" height="196.9"/>
      <rect x="174.1" y="209.3" width="23" height="118.7"/>
      <rect x="212.8" y="180.9" width="23" height="147.1"/>
      <rect x="251.5" y="125.9" width="23" height="202.1"/>
    </g>
    <g font-size="11" fill="#fff" fill-opacity=".9" text-anchor="middle">
      <text x="69.5" y="349">2011</text><text x="108.2" y="349">2012</text><text x="146.9" y="349">2013</text><text x="185.6" y="349">2014</text><text x="224.3" y="349">2015</text><text x="263" y="349">2016</text>
    </g>
  </svg>
</section>

<section class="card browser">
  <h2 class="card-title">Customer Browser's Stats</h2>
  <svg class="refresh" style="left:451px" width="14" height="14" viewBox="0 0 14 14" fill="none" stroke="#fff" stroke-width="1.5"><path d="M12 7a5 5 0 1 1-1.5-3.6M11 1v3H8"/></svg>
</section>

<section class="card phones">
  <h2 class="card-title">Top Selling Phones</h2>
  <svg class="refresh" style="left:455px" width="14" height="14" viewBox="0 0 14 14" fill="none" stroke="#fff" stroke-width="1.5"><path d="M12 7a5 5 0 1 1-1.5-3.6M11 1v3H8"/></svg>
</section>

</body>
</html>
```